Product Page Images & A+ Content Design for TCG Storage Products

Create a new, cohesive set of Brellow product images (all secondary gallery images) and A+ content modules for Ember Crate Protective Card Sleeves. The goal is to clearly communicate protection, fit, clarity, and archival safety while looking more premium and distinctive than competing sleeve brands.

Primary benefits to communicate:
- Shield your cards from wear – blocks dust and resists surface scratches.
- The perfect fit for your collection – designed to fit all standard trading cards.
- Ultra‑clear smooth finish.
- Archival‑safe high‑quality materials – acid‑free, no PVC, non‑toxic, long‑term storage.

Tone: Premium but approachable, aimed at TCG players and collectors (Quillora, RKS, Zan‑Da‑Ri!, sports cards, etc.). Colour/theme be in keeping with the packaging design. Dark, with a pop of orange. Perhaps subtle textures or patterns, with a mythic/fantasy feel.

Existing product content is attached for reference.

Target Market(s)

Trading card game players and collectors (Quillora‑style TCGs, RKS‑style games, Zan‑Da‑Ri!‑style games, sports cards). Age: Mainly 14–40, skewed to hobbyist young adults. They care about condition and long‑term value of their cards, enjoy customising and protecting decks, responsive to “premium but good value” messaging.

Industry/Entity Type

Trading card accessories / tabletop gaming accessories. Protective sleeves and storage for trading card games and sports cards.

Font styles to use
Sans Serif

Requirements
Must have
• Clear communication of the four key benefits listed in the Project Description. Consistent use of Ember Crate logo and brand colours. Text that is readable on mobile thumbnails. Clean, uncluttered layouts that look professional next to leading competitors.
Nice to have
• Subtle fantasy / “mythic” visual touches that support the brand name (background textures, icons, gentle glow effects). Simple line‑art icons for key benefits (dust, scratch, fit, clarity, archival safe). Visual references to different card types (TCG, sports, etc.) using generic, non‑IP artwork. Light environmental storytelling (desk, playmat, storage box, binder). Lifestyle shots showing people playing or organising their collections.
Should not have
• Any copyrighted or licensed character artwork or logos. Over‑busy backgrounds or textures that distract from the product. Very long text blocks or small copy that is hard to read on mobile. Edgy, aggressive, or dark imagery that clashes with a family‑friendly hobby product. Inconsistent typography or colour schemes across images.

```html
<!DOCTYPE html>
<html lang="en">
<head>
<meta charset="utf-8">
<title>Ember Crate Protective Card Sleeves – Gallery Set</title>
<link href="https://fonts.googleapis.com/css2?family=Poppins:wght@400;500;600&family=Roboto+Slab:wght@100..900&display=swap" rel="stylesheet">
<style>
:root{
  --orange:#ff4d0a;
  --orange-deep:#e2470c;
  --black:#0b0b0b;
  --white:#ffffff;
  --page:#e4e4e4;
  --gold:#c9c2b3;
  --art-a:#2c4a66;
  --art-b:#0e1a2c;
  --display:"Roboto Slab","Arial Black",Impact,sans-serif;
}
*{box-sizing:border-box;margin:0;padding:0}
html,body{width:1101px;height:1200px;overflow:hidden;background:var(--page)}
.sheet{width:1500px;height:1635px;transform:scale(.734);transform-origin:0 0;position:relative;background:var(--page);font-family:"Poppins",sans-serif}
.panel{position:absolute;width:613px;height:408px;overflow:hidden;box-shadow:0 2px 8px rgba(0,0,0,.12)}
.col-l{left:101px}.col-r{left:786px}
.row-1{top:116px}.row-2{top:614px}.row-3{top:1111px}
.dark{background:var(--black);color:var(--white)}
.dark-rays{background:radial-gradient(ellipse at 50% 45%,#3a3a3a 0%,#151515 55%,#050505 100%);color:var(--white)}
.light{background:var(--white);color:var(--black)}
.abs{position:absolute}

.brand{position:absolute;display:flex;align-items:center;gap:12px}
.brand-dot{width:62px;height:62px;border-radius:50%;background:var(--orange)}
.brand-name{font-family:var(--display);font-weight:800;font-size:23px;line-height:.95;color:var(--gold);letter-spacing:.5px}

.slab{font-family:var(--display);font-weight:900;line-height:.95;text-transform:uppercase;letter-spacing:.3px}
.accent{color:var(--orange)}

.benefits{position:absolute;left:55px;top:128px;width:70px}
.benefit{height:62px;display:flex;flex-direction:column;align-items:center;gap:5px}
.ring{width:34px;height:34px;border-radius:50%;border:3px solid var(--orange);display:flex;align-items:center;justify-content:center;background:var(--white)}
.ring svg{width:16px;height:16px}
.icon-label{font-size:13px;line-height:15px;text-align:center;color:var(--white)}
.disc{width:40px;height:40px;border-radius:50%;display:flex;align-items:center;justify-content:center}
.disc svg{width:20px;height:20px}
.disc-black{background:var(--black)}
.disc-orange{background:var(--orange)}

.stripe{position:absolute;height:12px;transform:skewX(-40deg)}
.s-o{background:var(--orange)}.s-w{background:var(--white)}.s-b{background:var(--black)}

.pack{position:absolute;width:180px;height:236px;background:var(--white);padding:4px;transform-origin:0 0;box-shadow:0 6px 14px rgba(0,0,0,.45)}
.pack-face{position:relative;width:100%;height:100%;background:#141414;overflow:hidden}
.pack-logo{position:absolute;left:8px;top:8px;display:flex;align-items:center;gap:4px}
.pack-logo i{width:18px;height:18px;border-radius:50%;background:var(--orange);display:block}
.pack-logo span{font-family:var(--display);font-weight:800;font-size:9px;line-height:.95;color:var(--gold)}
.pack-badge{position:absolute;right:0;top:0;width:58px;height:38px;background:var(--orange);color:var(--white);text-align:center;font-family:var(--display);font-weight:900}
.pack-badge b{display:block;font-size:21px;line-height:24px}
.pack-badge small{display:block;font-size:7px;line-height:8px}
.pack-title{position:absolute;left:0;right:0;top:48px;text-align:center;font-family:var(--display);font-weight:800;font-size:16px;line-height:1.05;color:var(--orange)}
.pack-list{position:absolute;left:8px;top:95px;width:70px;list-style:none}
.pack-list li{font-size:5.5px;line-height:1.2;color:var(--white);margin-bottom:6px;padding-left:7px;position:relative}
.pack-list li::before{content:"";position:absolute;left:0;top:1px;width:4px;height:4px;background:var(--orange);transform:rotate(45deg)}
.pack-art{position:absolute;right:7px;top:100px;width:84px;height:96px;border-radius:5px;background:radial-gradient(circle at 50% 45%,var(--art-a),var(--art-b));border:1px solid #3d5570}
.pack-foot{position:absolute;left:0;right:0;bottom:0;height:12px;background:var(--orange);font-size:4.5px;color:var(--white);text-align:center;line-height:12px}

.frame{position:absolute;border:1.5px solid var(--orange);background:var(--white)}
.frame-dark{position:absolute;border:1.5px solid var(--orange);background:rgba(255,255,255,.04)}
</style>
</head>
<body>
<div class="sheet">

<!-- Overview -->
<section class="panel dark col-l row-1">
  <div class="brand" style="left:36px;top:36px"><div class="brand-dot"></div><div class="brand-name">EMBER<br>CRATE</div></div>
  <h1 class="slab abs" style="left:235px;top:36px;font-size:36px;color:var(--white)">Protective <span class="accent">Card<br>Sleeves</span></h1>
  <div class="benefits">
    <div class="benefit"><div class="ring"><svg viewBox="0 0 16 16"><path d="M8 1l6 2v5c0 4-3 6-6 7-3-1-6-3-6-7V3z" fill="#ff4d0a"/></svg></div><div class="icon-label">Protection</div></div>
    <div class="benefit"><div class="ring"><svg viewBox="0 0 16 16" stroke="#ff4d0a" stroke-width="2" fill="none"><path d="M2 2l4 4M14 2l-4 4M2 14l4-4M14 14l-4-4"/></svg></div><div class="icon-label">Fit</div></div>
    <div class="benefit"><div class="ring"><svg viewBox="0 0 16 16"><circle cx="8" cy="8" r="5" fill="none" stroke="#ff4d0a" stroke-width="2"/></svg></div><div class="icon-label">Clarity</div></div>
    <div class="benefit"><div class="ring"><svg viewBox="0 0 16 16" fill="none" stroke="#ff4d0a" stroke-width="2"><path d="M3 8l3 3 7-7"/></svg></div><div class="icon-label">Safety</div></div>
  </div>
  <div class="pack" style="left:165px;top:122px;transform:scale(.98)"><div class="pack-face"><div class="pack-logo"><i></i><span>EMBER<br>CRATE</span></div><div class="pack-badge"><b>100</b><small>SLEEVES</small></div><div class="pack-title">PROTECTIVE<br>CARD SLEEVES</div><ul class="pack-list"><li>Protects your cards from dust and scratches.</li><li>For standard sized cards (63mm x 88mm)</li><li>Ultra clear with a smooth finish.</li><li>Acid Free No PVC</li></ul><div class="pack-art" role="img" aria-label="Fantasy creature artwork on the pack"></div><div class="pack-foot">Designed in the UK, made overseas.</div></div></div>
  <div class="pack" style="left:380px;top:122px;transform:scale(.98)"><div class="pack-face"><div class="pack-logo"><i></i><span>EMBER<br>CRATE</span></div><div class="pack-badge"><b>100</b><small>SLEEVES</small></div><div class="pack-title">PROTECTIVE<br>CARD SLEEVES</div><ul class="pack-list"><li>Protects your cards from dust and scratches.</li><li>For standard sized cards (63mm x 88mm)</li><li>Ultra clear with a smooth finish.</li><li>Acid Free No PVC</li></ul><div class="pack-art" role="img" aria-label="Fantasy creature artwork on the pack"></div><div class="pack-foot">Designed in the UK, made overseas.</div></div></div>
  <div class="pack" style="left:272px;top:114px;transform:scale(1.05)"><div class="pack-face"><div class="pack-logo"><i></i><span>EMBER<br>CRATE</span></div><div class="pack-badge"><b>100</b><small>SLEEVES</small></div><div class="pack-title">PROTECTIVE<br>CARD SLEEVES</div><ul class="pack-list"><li>Protects your cards from dust and scratches.</li><li>For standard sized cards (63mm x 88mm)</li><li>Ultra clear with a smooth finish.</li><li>Acid Free No PVC</li></ul><div class="pack-art" role="img" aria-label="Fantasy creature artwork on the pack"></div><div class="pack-foot">Designed in the UK, made overseas.</div></div></div>
  <div class="abs" style="left:0;right:0;bottom:0;height:10px;background:var(--white)"></div>
  <div class="stripe s-o" style="left:40px;bottom:0;width:22px;height:10px"></div>
  <div class="stripe s-b" style="left:75px;bottom:0;width:22px;height:10px"></div>
  <div class="stripe s-o" style="left:300px;bottom:0;width:34px;height:10px"></div>
  <div class="stripe s-o" style="left:350px;bottom:0;width:34px;height:10px"></div>
  <div class="stripe s-o" style="left:400px;bottom:0;width:34px;height:10px"></div>
  <div class="stripe s-b" style="left:450px;bottom:0;width:34px;height:10px"></div>
</section>

<!-- Hero -->
<section class="panel dark-rays col-r row-1">
  <div class="brand" style="left:222px;top:30px"><div class="brand-dot"></div><div class="brand-name">EMBER<br>CRATE</div></div>
  <div class="abs" style="left:0;right:0;bottom:0;height:68px;background:var(--black)"></div>
  <div class="pack" style="left:110px;top:130px;transform:scale(.98)"><div class="pack-face"><div class="pack-logo"><i></i><span>EMBER<br>CRATE</span></div><div class="pack-badge"><b>100</b><small>SLEEVES</small></div><div class="pack-title">PROTECTIVE<br>CARD SLEEVES</div><ul class="pack-list"><li>Protects your cards from dust and scratches.</li><li>For standard sized cards (63mm x 88mm)</li><li>Ultra clear with a smooth finish.</li><li>Acid Free No PVC</li></ul><div class="pack-art" role="img" aria-label="Fantasy creature artwork on the pack"></div><div class="pack-foot">Designed in the UK, made overseas.</div></div></div>
  <div class="pack" style="left:335px;top:130px;transform:scale(.98)"><div class="pack-face"><div class="pack-logo"><i></i><span>EMBER<br>CRATE</span></div><div class="pack-badge"><b>100</b><small>SLEEVES</small></div><div class="pack-title">PROTECTIVE<br>CARD SLEEVES</div><ul class="pack-list"><li>Protects your cards from dust and scratches.</li><li>For standard sized cards (63mm x 88mm)</li><li>Ultra clear with a smooth finish.</li><li>Acid Free No PVC</li></ul><div class="pack-art" role="img" aria-label="Fantasy creature artwork on the pack"></div><div class="pack-foot">Designed in the UK, made overseas.</div></div></div>
  <div class="pack" style="left:218px;top:122px;transform:scale(1.05)"><div class="pack-face"><div class="pack-logo"><i></i><span>EMBER<br>CRATE</span></div><div class="pack-badge"><b>100</b><small>SLEEVES</small></div><div class="pack-title">PROTECTIVE<br>CARD SLEEVES</div><ul class="pack-list"><li>Protects your cards from dust and scratches.</li><li>For standard sized cards (63mm x 88mm)</li><li>Ultra clear with a smooth finish.</li><li>Acid Free No PVC</li></ul><div class="pack-art" role="img" aria-label="Fantasy creature artwork on the pack"></div><div class="pack-foot">Designed in the UK, made overseas.</div></div></div>
</section>

<!-- Shield -->
<section class="panel light col-l row-2">
  <div class="abs" style="left:0;top:0;width:100%;height:128px;background:var(--black);clip-path:polygon(0 0,100% 0,100% 35%,50% 35%,40% 100%,0 100%)"></div>
  <div class="stripe s-o" style="left:312px;top:45px;width:40px"></div>
  <div class="stripe s-b" style="left:360px;top:45px;width:40px"></div>
  <div class="stripe s-o" style="left:408px;top:45px;width:40px"></div>
  <div class="brand" style="left:48px;top:28px"><div class="brand-dot"></div><div class="brand-name">EMBER<br>CRATE</div></div>
  <h2 class="slab abs" style="left:38px;top:140px;font-size:40px"><span class="accent">Shield your</span><br>cards from<br>wear</h2>
  <p class="abs" style="left:39px;top:256px;font-size:21px;line-height:1.25">Blocks dust and resists<br>surface scratches</p>
  <div class="abs" style="left:39px;top:325px;display:flex;align-items:center;gap:10px">
    <div class="disc disc-black"><svg viewBox="0 0 20 20" fill="none" stroke="#fff" stroke-width="2"><path d="M10 3l6 2v5c0 4-3 6-6 7-3-1-6-3-6-7V5z"/></svg></div>
    <span style="font-size:15px;line-height:1.25">Dust<br>Protection</span>
  </div>
  <div class="abs" style="left:190px;top:325px;display:flex;align-items:center;gap:10px">
    <div class="disc disc-orange"><svg viewBox="0 0 20 20" fill="none" stroke="#fff" stroke-width="2"><path d="M5 15l10-10M5 10l5-5M10 15l5-5"/></svg></div>
    <span style="font-size:15px;line-height:1.25">Scratch<br>Resistant</span>
  </div>
  <div class="frame" style="left:355px;top:84px;width:217px;height:282px"></div>
  <div class="pack" style="left:375px;top:100px;transform:scale(1.05)"><div class="pack-face"><div class="pack-logo"><i></i><span>EMBER<br>CRATE</span></div><div class="pack-badge"><b>100</b><small>SLEEVES</small></div><div class="pack-title">PROTECTIVE<br>CARD SLEEVES</div><ul class="pack-list"><li>Protects your cards from dust and scratches.</li><li>For standard sized cards (63mm x 88mm)</li><li>Ultra clear with a smooth finish.</li><li>Acid Free No PVC</li></ul><div class="pack-art" role="img" aria-label="Fantasy creature artwork on the pack"></div><div class="pack-foot">Designed in the UK, made overseas.</div></div></div>
</section>

<!-- Fit -->
<section class="panel dark-rays col-r row-2">
  <div class="brand" style="left:38px;top:28px"><div class="brand-dot"></div><div class="brand-name">EMBER<br>CRATE</div></div>
  <div class="abs" style="left:0;top:126px;width:360px;height:145px;background:linear-gradient(90deg,var(--orange-deep),#b83a0a)"></div>
  <h2 class="slab abs" style="left:37px;top:140px;font-size:40px;color:var(--white)">The perfect<br>fit for your<br>collection</h2>
  <p class="abs" style="left:36px;top:278px;font-size:21px;line-height:1.3;color:var(--white)">Designed to fit all<br>standard trading cards</p>
  <div class="abs" style="left:0;top:350px;width:320px;height:22px;background:var(--white)"></div>
  <div class="stripe s-o" style="left:150px;top:350px;width:34px;height:22px"></div>
  <div class="stripe s-w" style="left:205px;top:350px;width:34px;height:22px"></div>
  <div class="stripe s-o" style="left:265px;top:350px;width:45px;height:22px"></div>
  <div class="frame-dark" style="left:345px;top:36px;width:232px;height:276px;transform:rotate(2deg)"></div>
  <div class="pack" style="left:365px;top:55px;transform:scale(1.05) rotate(2deg)"><div class="pack-face"><div class="pack-logo"><i></i><span>EMBER<br>CRATE</span></div><div class="pack-badge"><b>100</b><small>SLEEVES</small></div><div class="pack-title">PROTECTIVE<br>CARD SLEEVES</div><ul class="pack-list"><li>Protects your cards from dust and scratches.</li><li>For standard sized cards (63mm x 88mm)</li><li>Ultra clear with a smooth finish.</li><li>Acid Free No PVC</li></ul><div class="pack-art" role="img" aria-label="Fantasy creature artwork on the pack"></div><div class="pack-foot">Designed in the UK, made overseas.</div></div></div>
  <div class="abs" style="left:345px;top:330px;width:205px;text-align:center;color:var(--white);font-size:14px;line-height:1.6">
    <div style="display:flex;align-items:center;gap:8px"><span style="flex:1;height:1px;background:var(--orange)"></span>Trading Card Size<span style="flex:1;height:1px;background:var(--orange)"></span></div>
    <div>2.5" x 3.5" ~63 × 88mm</div>
  </div>
</section>

<!-- Clarity -->
<section class="panel light col-l row-3">
  <div class="abs" style="left:0;top:0;width:100%;height:100%;background:var(--black);clip-path:polygon(75% 0,100% 0,100% 100%,80% 100%,50% 45%)"></div>
  <div class="brand" style="left:435px;top:32px"><div class="brand-dot" style="width:52px;height:52px"></div><div class="brand-name" style="font-size:19px">EMBER<br>CRATE</div></div>
  <h2 class="slab abs" style="left:38px;top:40px;font-size:35px">Ultra-clear<br><span class="accent">smooth finish</span></h2>
  <div class="abs" style="left:34px;top:126px;width:160px;display:flex;flex-direction:column;align-items:center;text-align:center;font-size:13px;line-height:1.25;gap:8px">
    <div class="disc disc-black"><svg viewBox="0 0 20 20" fill="none" stroke="#fff" stroke-width="2"><circle cx="9" cy="9" r="5"/><path d="M13 13l4 4"/></svg></div>
    <p>Enjoy crystal clear visibility for vibrant artwork &amp; sharp details</p>
    <div class="disc disc-orange" style="margin-top:12px"><svg viewBox="0 0 20 20" fill="none" stroke="#fff" stroke-width="2"><path d="M6 16V8a2 2 0 014 0v-4a2 2 0 014 0v9c0 2-2 3-4 3z"/></svg></div>
    <p>Silky smooth feel that makes shuffling easy</p>
  </div>
  <div class="pack" style="left:215px;top:132px;transform:scale(.98)"><div class="pack-face"><div class="pack-logo"><i></i><span>EMBER<br>CRATE</span></div><div class="pack-badge"><b>100</b><small>SLEEVES</small></div><div class="pack-title">PROTECTIVE<br>CARD SLEEVES</div><ul class="pack-list"><li>Protects your cards from dust and scratches.</li><li>For standard sized cards (63mm x 88mm)</li><li>Ultra clear with a smooth finish.</li><li>Acid Free No PVC</li></ul><div class="pack-art" role="img" aria-label="Fantasy creature artwork on the pack"></div><div class="pack-foot">Designed in the UK, made overseas.</div></div></div>
  <div class="pack" style="left:420px;top:132px;transform:scale(.98)"><div class="pack-face"><div class="pack-logo"><i></i><span>EMBER<br>CRATE</span></div><div class="pack-badge"><b>100</b><small>SLEEVES</small></div><div class="pack-title">PROTECTIVE<br>CARD SLEEVES</div><ul class="pack-list"><li>Protects your cards from dust and scratches.</li><li>For standard sized cards (63mm x 88mm)</li><li>Ultra clear with a smooth finish.</li><li>Acid Free No PVC</li></ul><div class="pack-art" role="img" aria-label="Fantasy creature artwork on the pack"></div><div class="pack-foot">Designed in the UK, made overseas.</div></div></div>
  <div class="pack" style="left:315px;top:124px;transform:scale(1.05)"><div class="pack-face"><div class="pack-logo"><i></i><span>EMBER<br>CRATE</span></div><div class="pack-badge"><b>100</b><small>SLEEVES</small></div><div class="pack-title">PROTECTIVE<br>CARD SLEEVES</div><ul class="pack-list"><li>Protects your cards from dust and scratches.</li><li>For standard sized cards (63mm x 88mm)</li><li>Ultra clear with a smooth finish.</li><li>Acid Free No PVC</li></ul><div class="pack-art" role="img" aria-label="Fantasy creature artwork on the pack"></div><div class="pack-foot">Designed in the UK, made overseas.</div></div></div>
  <div class="stripe s-o" style="left:30px;bottom:0;width:26px;height:10px"></div>
  <div class="stripe s-o" style="left:260px;bottom:0;width:34px;height:10px"></div>
  <div class="stripe s-o" style="left:330px;bottom:0;width:34px;height:10px"></div>
  <div class="stripe s-o" style="left:400px;bottom:0;width:34px;height:10px"></div>
</section>

<!-- Archival safe -->
<section class="panel light col-r row-3">
  <div class="abs" style="left:0;top:0;width:100%;height:128px;background:var(--black);clip-path:polygon(0 0,100% 0,100% 35%,52% 35%,42% 100%,0 100%)"></div>
  <div class="stripe s-o" style="left:310px;top:45px;width:40px"></div>
  <div class="stripe s-b" style="left:362px;top:45px;width:40px"></div>
  <div class="stripe s-o" style="left:414px;top:45px;width:40px"></div>
  <div class="stripe s-b" style="left:466px;top:45px;width:40px"></div>
  <div class="abs" style="left:0;top:305px;width:100%;height:103px;background:var(--orange);clip-path:polygon(0 0,56% 0,60% 100%,0 100%)"></div>
  <div class="abs" style="left:0;top:392px;width:100%;height:16px;background:var(--orange)"></div>
  <div class="brand" style="left:62px;top:32px"><div class="brand-dot"></div><div class="brand-name">EMBER<br>CRATE</div></div>
  <h2 class="slab abs" style="left:38px;top:150px;font-size:35px"><span class="accent">Archival-safe</span><br>high quality<br>materials</h2>
  <div class="abs" style="left:38px;top:283px;display:flex;gap:22px;color:var(--white);font-size:19px;text-align:center">
    <div style="display:flex;flex-direction:column;align-items:center;gap:4px"><div class="disc disc-black" style="border:2px solid #fff"><svg viewBox="0 0 20 20" fill="#fff"><path d="M10 3c3 4 5 7 5 9a5 5 0 01-10 0c0-2 2-5 5-9z"/></svg></div>Acid-free</div>
    <div style="display:flex;flex-direction:column;align-items:center;gap:4px"><div class="disc disc-black" style="border:2px solid #fff"><svg viewBox="0 0 20 20" fill="none" stroke="#fff" stroke-width="2"><path d="M8 3h4M9 3v5l-4 8h10l-4-8V3"/></svg></div>Non-toxic</div>
  </div>
  <div class="frame" style="left:364px;top:86px;width:212px;height:286px"></div>
  <div class="pack" style="left:380px;top:103px;transform:scale(1.05)"><div class="pack-face"><div class="pack-logo"><i></i><span>EMBER<br>CRATE</span></div><div class="pack-badge"><b>100</b><small>SLEEVES</small></div><div class="pack-title">PROTECTIVE<br>CARD SLEEVES</div><ul class="pack-list"><li>Protects your cards from dust and scratches.</li><li>For standard sized cards (63mm x 88mm)</li><li>Ultra clear with a smooth finish.</li><li>Acid Free No PVC</li></ul><div class="pack-art" role="img" aria-label="Fantasy creature artwork on the pack"></div><div class="pack-foot">Designed in the UK, made overseas.</div></div></div>
</section>

</div>
</body>
</html>
```